Group training gym/bootcamp needs a web design

We need a website for our gym that is based in Sydney. We have indoor functional training classes and outdoor bootcamp classes. We would like the web site to have a video (to be created) and photo gallery. I would like the site made on word press and i would like to be able to make minor changes such as changing images and text without having to use a designer.

The website should have the following pages: home page; the gym; the bootcamp; photo gallery; about us; contact.

I have uploaded our logo and i would like to keep to these colour (blue,yellow,silver) and black is also allowed

Target Market(s)

18-50 male and female

Industry/Entity Type

Gym

Coding

Coded - Design and coding required

Number of Pages Required

5+ page

Font styles to use
Sans Serif

Colors
0692cd
fbed22
1b1b1b
e8e8e8

Requirements
Must have
• The website should have the following pages: home page; the gym; the bootcamp; photo gallery; about us; contact.
• I have uploaded our logo and i would like to keep to these colour (blue,yellow,silver) and black is also allowed
• Video upload and photo upload

```html
<!DOCTYPE html>
<html lang="en">
<head>
<meta charset="utf-8">
<title>Corefield Training Co — Group Training Sydney</title>
<link rel="stylesheet" href="https://fonts.googleapis.com/css2?family=Oswald:wght@400;500;700&family=Open+Sans:wght@400;600;700&display=swap">
<style>
:root{
  --blue:#0692cd;
  --yellow:#fbed22;
  --gold:#f2c500;
  --black:#1b1b1b;
  --silver:#e8e8e8;
  --grey-text:#6a6a6a;
  --white:#ffffff;
}
*{margin:0;padding:0;box-sizing:border-box}
html,body{width:1200px;height:4000px;overflow:hidden}
body{position:relative;background:var(--white);font-family:"Open Sans",Arial,sans-serif;color:var(--black)}
.abs{position:absolute}
.display{font-family:"Oswald","Arial Narrow",sans-serif}

/* header */
.site-header{left:0;top:0;width:1200px;height:150px;background:var(--white)}
.brand{left:120px;top:18px;display:flex;align-items:center;gap:12px}
.brand-mark{width:46px;height:46px;background:var(--blue);border-radius:6px}
.brand-name{font-family:"Oswald",sans-serif;font-weight:700;font-size:22px;line-height:1.05;color:var(--blue);text-transform:uppercase;width:170px}
.call{left:720px;top:28px;display:flex;gap:10px;align-items:center}
.call-icon{width:34px;height:34px;border-radius:50%;background:var(--yellow);display:flex;align-items:center;justify-content:center}
.call small{display:block;font-size:11px;color:var(--grey-text);letter-spacing:1px}
.call strong{font-size:15px;color:var(--blue)}
.social{left:955px;top:36px;display:flex;gap:8px}
.social span{width:22px;height:22px;border-radius:50%;background:var(--blue)}
.main-nav{left:448px;top:104px;display:flex;gap:6px}
.main-nav a{font-size:12px;font-weight:600;color:var(--black);text-decoration:none;padding:7px 14px;text-transform:uppercase}
.main-nav a.active{background:var(--blue);color:var(--white)}

/* hero */
.hero{left:0;top:150px;width:1200px;height:580px;background:linear-gradient(90deg,#6d6d6d 0%,#9a9a9a 40%,#c9b54a 70%,var(--gold) 100%)}
.hero-title{left:830px;top:335px;color:var(--white);font-size:58px;line-height:1.05;text-transform:uppercase}
.hero-title b{font-weight:700;display:block}
.hero-title span{font-weight:400;display:block}
.btn-outline{border:2px solid var(--white);color:var(--white);font-size:14px;font-weight:700;padding:10px 18px;text-transform:uppercase;letter-spacing:1px}
.hero-btn{left:835px;top:600px}
.dots{left:560px;top:668px;display:flex;gap:10px}
.dots span{width:10px;height:10px;border-radius:50%;background:rgba(255,255,255,.6)}
.dots span.on{background:var(--white)}

/* section titles */
.section-title{width:1200px;left:0;text-align:center;font-family:"Oswald",sans-serif;font-size:30px;font-weight:400;color:var(--blue);text-transform:uppercase}
.section-title b{font-weight:700}
.section-title::after{content:"";display:block;width:60px;height:3px;background:var(--yellow);margin:10px auto 0}

/* services */
.services{left:130px;top:890px;width:940px;display:flex;justify-content:space-between}
.service{width:130px;text-align:center;font-size:13px;color:var(--black)}
.service .icon{width:96px;height:96px;border-radius:50%;background:var(--yellow);margin:0 auto 14px;display:flex;align-items:center;justify-content:center}

/* training */
.training-band{left:0;top:1060px;width:1200px;height:680px;background:var(--silver)}
.class-card{top:1270px;width:240px;height:250px}
.class-label{top:1540px;width:240px;font-family:"Oswald",sans-serif;font-weight:700;font-size:28px;color:var(--gold);text-transform:uppercase}
.class-overlay{left:110px;top:1270px;width:240px;height:250px;background:rgba(251,237,34,.9);padding:40px 30px;font-size:12px;color:var(--black)}
.btn-dark{display:inline-block;background:var(--black);color:var(--white);font-size:11px;font-weight:700;padding:8px 14px;margin-top:22px}

/* feature text */
.feature-title{font-family:"Oswald",sans-serif;font-size:36px;font-weight:700;color:var(--blue);text-transform:uppercase;line-height:1.15}
.feature-title span{display:block;font-weight:400;text-transform:none;font-size:34px}
.feature-copy{font-size:14px;line-height:1.7;color:var(--grey-text);width:300px;margin-top:28px}
.btn-yellow-outline{display:inline-block;border:2px solid var(--yellow);color:var(--blue);font-size:12px;font-weight:700;padding:9px 16px;margin-top:36px;text-transform:uppercase}

/* video */
.video-box{left:120px;top:2730px;width:360px;height:430px;background:var(--yellow);padding:36px 34px}
.video-box h3{font-family:"Oswald",sans-serif;font-size:34px;color:var(--blue);text-transform:uppercase}
.video-box p{font-size:13px;color:var(--black);margin-top:14px;line-height:1.6}
.thumbs{left:150px;top:2960px;width:310px;display:grid;grid-template-columns:repeat(4,70px);gap:10px}
.thumbs span{height:86px;background:linear-gradient(135deg,#c9c1a0,#5a7a90)}
.video-frame{left:480px;top:2730px;width:590px;height:430px;background:linear-gradient(120deg,#ededed,#c8c8c8)}
.play{left:722px;top:2910px;width:70px;height:70px;border-radius:50%;background:var(--yellow)}

/* gallery */
.gallery-band{left:0;top:3220px;width:1200px;height:420px;background:linear-gradient(180deg,#2a2a2a,#151515)}
.gallery-title{top:3275px;color:var(--white)}
.gallery-title b{color:var(--white)}
.shot{top:3400px;width:200px;height:200px;border:4px solid var(--white)}
.shot.on{border-color:var(--yellow)}
.arrow{top:3470px;width:40px;height:60px}

/* footer */
.site-footer{left:0;top:3640px;width:1200px;height:360px;background:var(--white)}
.foot-brand{left:140px;top:3720px;display:flex;align-items:center;gap:12px}
.foot-col{top:3710px}
.foot-col h4{font-size:13px;color:var(--blue);text-transform:uppercase;margin-bottom:12px}
.foot-col li{list-style:none;font-size:12px;color:var(--grey-text);line-height:1.9}
.input{width:230px;height:34px;border:1px solid #cfcfcf;font-size:12px;color:#999;padding:8px 10px}
.btn-signup{margin-top:14px;margin-left:140px;display:inline-block;background:var(--yellow);font-size:12px;font-weight:700;padding:8px 18px;color:var(--black)}
.copyright{left:0;top:3940px;width:1200px;border-top:1px solid #e2e2e2;padding-top:14px;text-align:center;font-size:11px;color:var(--grey-text)}
</style>
</head>
<body>

<header class="site-header abs">
  <div class="brand abs"><span class="brand-mark"></span><span class="brand-name">Corefield Training Co</span></div>
  <div class="call abs">
    <span class="call-icon"><svg width="16" height="16" viewBox="0 0 24 24"><path d="M6 2h4l2 5-3 2a11 11 0 0 0 6 6l2-3 5 2v4a2 2 0 0 1-2 2A18 18 0 0 1 4 4a2 2 0 0 1 2-2z" fill="#1b1b1b"/></svg></span>
    <div><small>CALL US NOW</small><strong>0400 123 456</strong></div>
  </div>
  <div class="social abs"><span></span><span></span><span></span><span></span><span></span></div>
  <nav class="main-nav abs">
    <a class="active">Home</a><a>The Gym</a><a>The Bootcamp</a><a>Photo Gallery</a><a>About Us</a><a>Contact Us</a>
  </nav>
</header>

<section class="hero abs" role="img" aria-label="Athlete lifting a barbell in the gym with a yellow light wash"></section>
<h1 class="hero-title abs display"><b>Indoor</b><b>Functional</b><span>Training</span><span>Classes</span></h1>
<span class="hero-btn btn-outline abs">Read More</span>
<div class="dots abs"><span class="on"></span><span></span><span></span><span></span><span></span></div>

<h2 class="section-title abs" style="top:775px">Our <b>Services</b></h2>
<div class="services abs">
  <div class="service"><div class="icon"><svg width="44" height="44" viewBox="0 0 24 24" fill="none" stroke="#1b1b1b" stroke-width="2"><circle cx="12" cy="12" r="9"/><path d="M12 7v5l3 2"/></svg></div>24 Hour Access</div>
  <div class="service"><div class="icon"><svg width="44" height="44" viewBox="0 0 24 24" fill="none" stroke="#1b1b1b" stroke-width="2"><rect x="7" y="6" width="10" height="15" rx="2"/><rect x="8" y="3" width="8" height="3"/></svg></div>Supplements</div>
  <div class="service"><div class="icon"><svg width="44" height="44" viewBox="0 0 24 24" fill="#1b1b1b"><circle cx="6" cy="8" r="2.5"/><circle cx="12" cy="7" r="2.5"/><circle cx="18" cy="8" r="2.5"/><rect x="4" y="12" width="4" height="8"/><rect x="10" y="11" width="4" height="9"/><rect x="16" y="12" width="4" height="8"/></svg></div>Group Fitness</div>
  <div class="service"><div class="icon"><svg width="44" height="44" viewBox="0 0 24 24" fill="#1b1b1b"><rect x="2" y="8" width="3" height="8"/><rect x="5" y="6" width="3" height="12"/><rect x="8" y="11" width="8" height="2"/><rect x="16" y="6" width="3" height="12"/><rect x="19" y="8" width="3" height="8"/></svg></div>Fitness Equipment</div>
  <div class="service"><div class="icon"><svg width="44" height="44" viewBox="0 0 24 24" fill="none" stroke="#1b1b1b" stroke-width="2"><circle cx="12" cy="12" r="9"/><path d="M8 12l3 3 5-6"/></svg></div>Guidance</div>
  <div class="service"><div class="icon"><svg width="44" height="44" viewBox="0 0 24 24" fill="none" stroke="#1b1b1b" stroke-width="2"><path d="M3 10l9-6 9 6v10H3z"/><path d="M9 20v-6h6v6"/></svg></div>Fitness Club</div>
</div>

<div class="training-band abs"></div>
<h2 class="section-title abs" style="top:1150px">Training <b>Classes</b></h2>
<div class="class-card abs" style="left:110px;background:linear-gradient(135deg,#e8dc3a,#c9b52a)" role="img" aria-label="Weight loss class photo"></div>
<div class="class-overlay abs">Burn fat and build stamina in fast, friendly group sessions led by our coaches.<br><span class="btn-dark">READ MORE</span></div>
<div class="class-card abs" style="left:350px;background:linear-gradient(135deg,#d9c8b8,#7fb6d4)" role="img" aria-label="Weight gain class photo with measuring tape"></div>
<div class="class-card abs" style="left:590px;background:linear-gradient(135deg,#3c3c3c,#1f4f7a)" role="img" aria-label="Body building class photo of push-ups"></div>
<div class="class-card abs" style="left:830px;background:linear-gradient(135deg,#2b2b2b,#8a8a8a)" role="img" aria-label="Body fitness class photo of a muscular torso"></div>
<div class="class-label abs" style="left:110px">Weight Loss</div>
<div class="class-label abs" style="left:350px">Weight Gain</div>
<div class="class-label abs" style="left:590px">Body Building</div>
<div class="class-label abs" style="left:830px">Body Fitness</div>

<div class="abs" style="left:130px;top:1830px">
  <h3 class="feature-title">Indoor Functional<span>training classes</span></h3>
  <p class="feature-copy">Our indoor classes mix strength, mobility and conditioning in small groups. Every session is coached, scaled to your level and built to keep you moving.</p>
  <span class="btn-yellow-outline">Read More &#8250;</span>
</div>
<div class="abs" style="left:520px;top:1770px;width:580px;height:460px;background:radial-gradient(circle at 55% 50%,#e6e6e6,#ffffff 70%)" role="img" aria-label="Couple doing a balance exercise on a fitness ball"></div>

<div class="abs" style="left:0;top:2240px;width:580px;height:450px;background:linear-gradient(180deg,#ffffff 0%,#f2f2f2 80%,#3a3a3a 80%,#2a2a2a 100%)" role="img" aria-label="Woman running outdoors in training gear"></div>
<div class="abs" style="left:700px;top:2320px">
  <h3 class="feature-title">Outdoor Bootcamp<span>classes</span></h3>
  <p class="feature-copy">Train in the fresh air across Sydney parks with high energy circuits, team drills and runs that push you further every week.</p>
  <span class="btn-yellow-outline">Read More &#8250;</span>
</div>

<div class="video-box abs">
  <h3>Our Video</h3>
  <p>See a class in action and meet the coaches who will train you.</p>
</div>
<div class="thumbs abs" role="img" aria-label="Grid of video thumbnails from training sessions"><span></span><span></span><span></span><span></span><span></span><span></span><span></span><span></span></div>
<div class="video-frame abs" role="img" aria-label="Video still of a woman stretching on a yoga mat"></div>
<div class="play abs"><svg width="70" height="70" viewBox="0 0 70 70"><path d="M28 22l22 13-22 13z" fill="#0692cd"/></svg></div>

<div class="gallery-band abs" role="img" aria-label="Dark gym background"></div>
<h2 class="section-title gallery-title abs">Photo <b>Gallery</b></h2>
<div class="shot abs" style="left:40px;background:linear-gradient(135deg,#c8a0a0,#7a6a6a)" role="img" aria-label="Group of women after a class"></div>
<div class="shot abs" style="left:260px;background:linear-gradient(135deg,#9fc6e0,#3a7aa8)" role="img" aria-label="Class doing floor exercises"></div>
<div class="shot on abs" style="left:480px;background:linear-gradient(135deg,#d8d8d8,#6a6a6a)" role="img" aria-label="Trainer guiding a member with weights"></div>
<div class="shot abs" style="left:700px;background:linear-gradient(135deg,#e0d0b8,#8a7a6a)" role="img" aria-label="Members training on mats"></div>
<div class="shot abs" style="left:920px;background:linear-gradient(135deg,#c0c0c0,#5a5a5a)" role="img" aria-label="Woman lifting dumbbells"></div>
<svg class="arrow abs" style="left:50px" viewBox="0 0 40 60"><path d="M28 10L10 30l18 20" stroke="#fff" stroke-width="6" fill="none"/></svg>
<svg class="arrow abs" style="left:1110px" viewBox="0 0 40 60"><path d="M12 10l18 20-18 20" stroke="#fff" stroke-width="6" fill="none"/></svg>

<footer class="site-footer abs"></footer>
<div class="foot-brand abs"><span class="brand-mark"></span><span class="brand-name">Corefield Training Co</span></div>
<div class="foot-col abs" style="left:430px">
  <h4>Menu</h4>
  <ul><li>Home</li><li>The Gym</li><li>The Bootcamp</li><li>Photo Gallery</li><li>About Us</li><li>Contact Us</li></ul>
</div>
<div class="foot-col abs" style="left:615px">
  <h4>Newsletter Signup</h4>
  <div class="input">Your email</div>
  <span class="btn-signup">SIGNUP</span>
</div>
<div class="foot-col abs" style="left:955px">
  <h4>Follow Us On</h4>
  <ul><li>&#9642; Social one</li><li>&#9642; Social two</li><li>&#9642; Social three</li><li>&#9642; Social four</li><li>&#9642; Social five</li></ul>
</div>
<div class="copyright abs">Copyright &copy; 2017 All Rights Reserved</div>

</body>
</html>
```